Card design for orthopaedic surgeons working as The Brightwater Joint Centre

Business cards, letterhead

Colors

Designer to choose colors to be used in the design.

Requirements
Must have
• Late addition.
• Cards letterhead must have logos of
• Crestmoor Lindell College of Surgeons
• Varenwood Bone Health Association
Nice to have
• Back of card to have space for appointment time to be added by hand and some blank space for writing incidental other notes.

```html
<!DOCTYPE html>
<html lang="en">
<head>
<meta charset="utf-8">
<title>The Brightwater Joint Centre – Business Card</title>
<link rel="stylesheet" href="https://fonts.googleapis.com/css2?family=Lato:wght@400&family=Poppins:wght@500&family=Raleway:wght@400&display=swap">
<style>
  :root {
    --backdrop: #2e2f31;
    --card-white: #ffffff;
    --sky: #33aefc;
    --navy: #0b2f4d;
    --ink: #1c1c1c;
    --rule: #9a9a9a;
  }
  * { margin: 0; padding: 0; box-sizing: border-box; }
  html, body { width: 1200px; height: 1200px; overflow: hidden; }
  body { background: var(--backdrop); position: relative; font-family: 'Lato', sans-serif; }

  .card {
    position: absolute;
    top: 310px;
    width: 365px;
    height: 594px;
    box-shadow: 0 4px 10px rgba(0,0,0,0.45);
    overflow: hidden;
  }
  .card--front { left: 234px; background: var(--card-white); }
  .card--back { left: 629px; background: var(--navy); }

  .brand-name {
    position: absolute;
    left: 0; right: 0;
    text-align: center;
    font-family: 'Raleway', sans-serif;
    font-weight: 400;
    font-size: 22.5px;
    letter-spacing: -0.3px;
    white-space: nowrap;
  }
  .card--front .brand-name { top: 180px; color: var(--navy); }
  .card--back .brand-name { top: 368px; color: var(--card-white); }

  .holder { position: absolute; top: 339px; left: 0; right: 0; text-align: center; }
  .holder-name { font-family: 'Poppins', sans-serif; font-weight: 500; font-size: 27px; line-height: 1; }
  .holder-name .first { color: var(--sky); }
  .holder-name .last { color: var(--navy); }
  .holder-role { font-size: 17px; color: var(--ink); margin-top: 0; }

  .icon-row { position: absolute; top: 396px; left: 87px; width: 190px; height: 24px; }

  .contact { position: absolute; left: 0; right: 0; text-align: center; font-size: 17.5px; color: var(--ink); line-height: 22px; }
  .contact--lines { top: 431px; }
  .contact--address { top: 517px; }
  .contact-divider { position: absolute; top: 507px; left: 88px; width: 196px; height: 1px; background: #c8c8c8; }

  .back-wave { position: absolute; left: 0; top: 0; }
  .back-site { position: absolute; top: 533px; left: 0; right: 0; text-align: center; font-family: 'Raleway', sans-serif; font-size: 18px; color: var(--card-white); }
  .back-site .accent { color: var(--sky); }
</style>
</head>
<body>
  <section class="card card--front" aria-label="Business card front">
    <p class="brand-name">The Brightwater Joint Centre</p>

    <div class="holder">
      <p class="holder-name"><span class="first">Daniel</span> <span class="last">Marlowe</span></p>
      <p class="holder-role">Managing Director</p>
    </div>

    <svg class="icon-row" viewBox="0 0 190 24" aria-hidden="true">
      <line x1="0" y1="12" x2="52" y2="12" stroke="var(--rule)" stroke-width="1.2"/>
      <line x1="138" y1="12" x2="190" y2="12" stroke="var(--rule)" stroke-width="1.2"/>
      <g class="icon icon--phone">
        <circle cx="67" cy="12" r="11.5" fill="var(--sky)"/>
        <circle cx="67" cy="12" r="9" fill="none" stroke="#fff" stroke-width="1"/>
        <rect x="61.5" y="11" width="11" height="6" rx="1.2" fill="#fff"/>
        <path d="M60 10 Q67 5 74 10 L72 11.5 Q67 8.5 62 11.5 Z" fill="#fff"/>
      </g>
      <g class="icon icon--mail">
        <circle cx="95" cy="12" r="11.5" fill="var(--sky)"/>
        <circle cx="95" cy="12" r="9" fill="none" stroke="#fff" stroke-width="1"/>
        <rect x="89" y="8" width="12" height="8.5" fill="#fff"/>
        <path d="M89 8 L95 13 L101 8" fill="none" stroke="var(--sky)" stroke-width="1"/>
      </g>
      <g class="icon icon--web">
        <circle cx="123" cy="12" r="11.5" fill="var(--sky)"/>
        <circle cx="123" cy="12" r="9" fill="none" stroke="#fff" stroke-width="1"/>
        <circle cx="123" cy="12" r="5.5" fill="#fff"/>
        <path d="M120 9 Q123 11 122 14 M125 8 Q126 12 124.5 16" fill="none" stroke="var(--sky)" stroke-width="1.2"/>
      </g>
    </svg>

    <div class="contact contact--lines">
      <p>061-270 318 452</p>
      <p>info@brightwaterjc.com</p>
      <p>www.brightwaterjc.com</p>
    </div>
    <div class="contact-divider"></div>
    <div class="contact contact--address">
      <p>738, Address line here,</p>
      <p>60917, Country Name</p>
    </div>
  </section>

  <section class="card card--back" aria-label="Business card back">
    <svg class="back-wave" width="365" height="594" viewBox="0 0 365 594" aria-hidden="true">
      <path d="M0 0 H365 V280 C330 300 290 312 250 300 C200 285 160 258 115 260 C70 262 30 285 0 318 Z" fill="var(--sky)"/>
    </svg>
    <p class="brand-name">The Brightwater Joint Centre</p>
    <p class="back-site">www.<span class="accent">brightwaterjc</span>.com</p>
  </section>
</body>
</html>
```